Velkora Land Surveying Website Design

We are working with Velkora. They are a national land surveying company and in need of a new website design.

Some sites to use for inspiration:

https://brannickeng.com
https://www.dvwinc.com
https://kelvarin.com
https://gto.us
https://ravendobuilt.com
https://www.marbeckquillondale.com

Thank you for taking the time to consider designing a website for us. We are web developers based in Stockton and Los Angeles, CA, USA. Most of our projects go through the same process. Understanding this process may help you win a project with us. We custom-code all of our websites in-house. We don’t have any requirements as to what tools you use for your design, but we prefer Figma files. For any design that we label as four-stars, we send it to the client for review. The client picks the final design they want us to use. Once we complete this process, we will continue to show additional clients all the four-star sites and purchase them later. Your designs will have multiple chances to sell. For better chances of success, we ask that you follow these guidelines.

IMAGES:
If you use any images or icons in the design, we ask that you have a link to the asset so we can purchase the image/icon. Most of the designs we submit do not have the customer’s images on them unless they have some great images. Be creative; show us the feeling you are trying to portray with your image choices. Use any royalty-free site you choose. We subscribe to Pellix and mainly use their images, but we can purchase images outside of Pellix.

PLEASE NOTE: we will not submit designs to clients with watermarks on the images.

FONTS:
We ask that you identify the fonts used in the design. This can be done in a message if you want. We typically use Google Fonts and Pellix Fonts.

CONTENT:
We're always open to different content and ideas. We often submit designs with stock images so the client can see our vision. We typically take pictures after the website launch to use their images with our vision. Lorem Ipsum is fine for paragraphs, but we ask that you write the headers in correct English. We want to be able to show the vision and identify the sections of the website.

INSPIRATION:
We typically add a couple of links in the brief of websites we like to help you get started in your design.

REVISIONS:
We do not often ask for revisions of the designs unless we see something in the design that may not appeal to the client. If there are slight changes that we want to make, we do that in the development process.

FEEDBACK:
We rarely give feedback on designs during the design process. We are working on many website projects and do not have the time to provide feedback. We usually respond if your request is well thought out and asks specific questions, but a note asking “feedback, please” usually goes unanswered.

```html
<!DOCTYPE html>
<html lang="en">
<head>
<meta charset="utf-8">
<title>Velkora Land Surveying</title>
<link href="https://fonts.googleapis.com/css2?family=Oswald:wght@400;500;600&family=Urbanist:wght@400;500;700&family=Lato:wght@400;700&family=Michroma&display=swap" rel="stylesheet">
<style>
:root{
  --red:#e0463a;
  --red-dark:#c8261b;
  --ink:#1d1d1d;
  --grey:#6b6b6b;
  --mist:#f4f4f4;
  --white:#ffffff;
  --black:#000000;
  --slate:#5f6560;
}
*{box-sizing:border-box;margin:0;padding:0}
html,body{width:1200px;height:3819px;overflow:hidden;background:var(--white)}
body{position:relative;font-family:"Urbanist",sans-serif;color:var(--ink)}
.abs{position:absolute}
.display{font-family:"Oswald",sans-serif;text-transform:uppercase}
.brand{font-family:"Oswald",sans-serif;font-weight:600;color:var(--red);letter-spacing:1px;display:flex;align-items:center;gap:12px}
.brand .dot{width:46px;height:46px;border-radius:50%;background:var(--red)}
.topbar{left:545px;top:0;width:655px;height:52px;background:var(--red);clip-path:polygon(0 0,100% 0,100% 100%,8% 100%);color:#fff;font-family:"Oswald",sans-serif;font-size:15px;display:flex;align-items:center;gap:50px;padding-left:80px}
.topbar span{display:flex;align-items:center;gap:10px}
.nav{top:84px;left:455px;display:flex;gap:0;font-family:"Oswald",sans-serif;font-size:17px}
.nav a{color:var(--ink);text-decoration:none;text-transform:uppercase;margin-right:42px}
.nav a.active{color:var(--red);text-decoration:underline}
.btn{display:inline-flex;align-items:center;border-radius:30px;overflow:hidden;font-family:"Oswald",sans-serif;text-transform:uppercase;color:#fff;height:48px}
.btn .label{background:var(--red);height:100%;display:flex;align-items:center;padding:0 24px 0 26px;clip-path:polygon(0 0,100% 0,88% 100%,0 100%);padding-right:34px}
.btn .arrow{background:#777;height:100%;width:52px;margin-left:-14px;display:flex;align-items:center;justify-content:center}
.hero{left:0;top:141px;width:1200px;height:580px;clip-path:polygon(0 0,100% 0,100% 449px,600px 575px,0 449px);background:linear-gradient(100deg,#6b6a62 0%,#8a7f6c 35%,#b08a5c 62%,#d9773a 78%,#6a7486 100%)}
.hero-shade{left:0;top:141px;width:1200px;height:580px;clip-path:polygon(0 0,100% 0,100% 449px,600px 575px,0 449px);background:linear-gradient(90deg,rgba(0,0,0,.45),rgba(0,0,0,0) 60%)}
.seal{width:84px;height:84px;border-radius:50%;background:#fff;box-shadow:0 2px 10px rgba(0,0,0,.15)}
.section-title{display:flex;align-items:center;justify-content:center;gap:14px;font-family:"Oswald",sans-serif;font-weight:500;color:var(--red);text-transform:uppercase}
.section-title .dot{width:36px;height:36px;border-radius:50%;background:var(--red)}
.kicker{font-size:18px;color:var(--grey);letter-spacing:.5px;text-transform:uppercase;font-weight:500}
.photo{background:linear-gradient(135deg,#8f8a76,#5e6a52)}
.card{background:#fff;border-radius:10px;box-shadow:0 6px 22px rgba(0,0,0,.07);overflow:hidden}
.card .img{height:193px}
.card .ic{position:absolute;left:50%;top:153px;margin-left:-40px;width:80px;height:80px;border-radius:50%;background:#fff;display:flex;align-items:center;justify-content:center}
.card h3{position:absolute;top:232px;width:100%;text-align:center;font-family:"Oswald",sans-serif;font-weight:500;font-size:22px;text-transform:uppercase}
.card p{position:absolute;top:276px;left:20px;right:20px;text-align:center;font-family:"Lato",sans-serif;font-size:16px;line-height:28px;color:#444}
.circ-arrow{width:38px;height:38px;border-radius:50%;display:flex;align-items:center;justify-content:center}
.quote .stars{color:#f5b301;font-size:20px;letter-spacing:1px}
.quote p{font-family:"Lato",sans-serif;font-size:16px;line-height:27.5px;color:#333;margin-top:18px}
.quote .who{display:flex;align-items:center;gap:14px;margin-top:26px}
.avatar{width:64px;height:64px;border-radius:50%;background:linear-gradient(135deg,#b9b1a6,#7d766d)}
.who b{display:block;font-family:"Michroma",sans-serif;font-size:13px;text-transform:uppercase;color:#111}
.who i{display:block;font-style:normal;font-family:"Michroma",sans-serif;font-size:12px;color:#999;text-transform:uppercase;margin-top:4px}
.footer h4{font-family:"Oswald",sans-serif;font-weight:400;font-size:19px;color:#fff;text-transform:uppercase;margin-bottom:18px}
.footer li{list-style:none;font-family:"Lato",sans-serif;font-size:16px;color:#fff;height:34px;display:flex;align-items:center;gap:10px}
.contact-row{display:flex;gap:14px;font-family:"Lato",sans-serif;font-size:16px;color:#fff;line-height:27px;margin-bottom:16px}
.contact-row .ci{width:32px;height:32px;border-radius:50%;background:#fff;flex:none;display:flex;align-items:center;justify-content:center}
</style>
</head>
<body>

<!-- Header -->
<div class="abs topbar">
  <span><svg width="18" height="18" viewBox="0 0 24 24"><path fill="#fff" d="M6.6 10.8a15 15 0 006.6 6.6l2.2-2.2c.3-.3.7-.4 1-.2 1.1.4 2.3.6 3.6.6.6 0 1 .4 1 1V20c0 .6-.4 1-1 1C10.6 21 3 13.4 3 4c0-.6.4-1 1-1h3.5c.6 0 1 .4 1 1 0 1.2.2 2.4.6 3.6.1.3 0 .7-.2 1z"/></svg>Call:+1 555 014 2290</span>
  <span><svg width="18" height="14" viewBox="0 0 24 18"><rect width="24" height="18" rx="2" fill="#fff"/><path d="M1 1l11 8 11-8" stroke="#e0463a" stroke-width="2" fill="none"/></svg>Mail:info@velkorals.com</span>
</div>
<div class="abs brand" style="left:100px;top:38px;font-size:32px"><span class="dot"></span>Velkora Land Surveying</div>
<nav class="abs nav">
  <a class="active">Home</a><a>About</a><a>Services</a><a>Testimonials</a><a>Blog</a>
</nav>
<div class="abs btn" style="left:950px;top:70px;height:42px;font-size:15px">
  <span class="label">Contact Us</span><span class="arrow"><svg width="18" height="12" viewBox="0 0 18 12"><path d="M0 6h16M11 1l5 5-5 5" stroke="#fff" stroke-width="1.8" fill="none"/></svg></span>
</div>

<!-- Hero -->
<div class="abs hero" role="img" aria-label="Surveyor in hard hat and safety vest looking through a total station on a tripod at a construction site"></div>
<div class="abs hero-shade"></div>
<div class="abs" style="left:600px;top:712px;width:600px;height:716px;background:var(--mist);clip-path:polygon(0 0,100% 0,100% 100%,54% 100%)"></div>
<div class="abs" style="left:600px;top:590px;width:600px;height:125px;background:var(--mist);clip-path:polygon(0 100%,100% 0,100% 100%)"></div>
<div class="abs display" style="left:105px;top:236px;font-size:58px;font-weight:500;color:var(--red);line-height:1">Precision. Expertise.</div>
<div class="abs display" style="left:105px;top:300px;font-size:72px;font-weight:500;color:#fff;line-height:1">Every Point Matters.</div>
<div class="abs" style="left:106px;top:390px;width:600px;font-family:'Lato',sans-serif;font-size:17px;line-height:31px;color:#fff">Velkora delivers accurate, reliable land surveying solutions across Australia — from urban developments to remote sites.</div>
<div class="abs btn" style="left:105px;top:470px;height:50px;font-size:20px">
  <span class="label">Get Started</span><span class="arrow"><svg width="20" height="14" viewBox="0 0 18 12"><path d="M0 6h16M11 1l5 5-5 5" stroke="#fff" stroke-width="1.8" fill="none"/></svg></span>
</div>
<div class="abs" style="left:578px;top:672px;display:flex;gap:8px">
  <span style="width:9px;height:9px;border-radius:50%;background:rgba(255,255,255,.45)"></span>
  <span style="width:9px;height:9px;border-radius:50%;background:#fff"></span>
  <span style="width:9px;height:9px;border-radius:50%;background:rgba(255,255,255,.45)"></span>
</div>
<div class="abs seal" style="left:558px;top:714px"></div>

<!-- About -->
<div class="abs" style="left:332px;top:875px;width:268px;height:201px;background:linear-gradient(180deg,#e0a24a,#a8742e)" role="img" aria-label="Aerial view of farmland at sunset with location pins"></div>
<div class="abs photo" style="left:107px;top:924px;width:266px;height:398px;border-right:8px solid #fff;border-top:8px solid #fff;background:linear-gradient(160deg,#a9aba5,#7b8068 60%,#6a7a3a)" role="img" aria-label="Hands operating a green total station at a quarry site"></div>
<div class="abs" style="left:382px;top:1090px;width:218px;height:222px;background:linear-gradient(135deg,#d94a3a,#a66a56);box-shadow:0 8px 20px rgba(0,0,0,.15)"></div>
<div class="abs" style="left:460px;top:1118px;color:#fff;font-family:'Michroma',sans-serif;font-size:28px">20+</div>
<div class="abs" style="left:460px;top:1160px;color:#fff;font-family:'Urbanist',sans-serif;font-size:21px;line-height:31px">Years<br>of<br>experience</div>
<div class="abs" style="left:460px;top:1256px;color:#f5b301;font-size:18px">★★★★★</div>

<div class="abs section-title" style="left:650px;top:862px;font-size:46px;justify-content:flex-start"><span class="dot" style="width:40px;height:40px"></span>About Velkora</div>
<div class="abs kicker" style="left:660px;top:924px">Land Surveying</div>
<div class="abs" style="left:662px;top:960px;font-size:17px;font-weight:700;color:var(--red)">We have over 20 years' experience</div>
<div class="abs" style="left:660px;top:994px;width:436px;font-family:'Lato',sans-serif;font-size:14px;line-height:26px;color:#333">Lorem ipsum dolor sit amet, consectetur adipiscing elit, sed do eiusmod tempor incididunt ut labore et dolore magna aliqua. Ut enim ad minim veniam, quis nostrud exercitation ullamco laboris nisi ut aliquip ex ea commodo consequat.<br><br>Duis aute irure dolor in reprehenderit in voluptate velit esse cillum dolore eu fugiat nulla pariatur. Excepteur sint labore et dolore magna aliqua. Ut enim ad minim veniam, quis nostrud exercitation ullamco laboris nisi ut aliquipoccaecat cupidatat non proident, sunt in culpa qui officia deserunt mollit anim id est laborum.</div>
<div class="abs btn" style="left:651px;top:1267px;height:50px;font-size:17px">
  <span class="label">Read More</span><span class="arrow"><svg width="20" height="14" viewBox="0 0 18 12"><path d="M0 6h16M11 1l5 5-5 5" stroke="#fff" stroke-width="1.8" fill="none"/></svg></span>
</div>

<!-- Services -->
<div class="abs" style="left:0;top:1428px;width:1200px;height:665px;background:var(--mist)"></div>
<div class="abs section-title" style="left:0;top:1478px;width:1200px;font-size:46px"><span class="dot"></span>Our Services</div>
<div class="abs kicker" style="left:0;top:1543px;width:1200px;text-align:center">We Offer</div>

<div class="abs card" style="left:107px;top:1610px;width:295px;height:388px">
  <div class="img" style="background:linear-gradient(180deg,#7f8a55,#5a4a34)" role="img" aria-label="Boundary marker post with orange paint in a grassy field"></div>
  <div class="ic"><svg width="40" height="36" viewBox="0 0 40 36" fill="none" stroke="#e0463a" stroke-width="2.4"><rect x="4" y="4" width="8" height="8"/><rect x="28" y="4" width="8" height="8"/><rect x="4" y="24" width="8" height="8"/><rect x="26" y="22" width="10" height="10" fill="#e0463a"/><path d="M12 8h16M8 12v12M12 28h14"/></svg></div>
  <h3>Boundary Surveys</h3>
  <p>Excepteur sint occaecat cupidatat non proident, sunt in culpa qui officiaan</p>
</div>
<div class="abs card" style="left:452px;top:1610px;width:296px;height:388px">
  <div class="img" style="background:linear-gradient(135deg,#4c6a3a,#2f4a2a)" role="img" aria-label="Aerial view of a wooded neighbourhood with map pins and linework"></div>
  <div class="ic"><svg width="40" height="40" viewBox="0 0 40 40" fill="none" stroke="#e0463a" stroke-width="2.4"><circle cx="28" cy="8" r="4" fill="#e0463a"/><rect x="12" y="6" width="10" height="8"/><path d="M17 14v4M17 18l-8 18M17 18v18M17 18l8 18"/></svg></div>
  <h3>Topographic Surveys</h3>
  <p>Excepteur sint occaecat cupidatat non proident, sunt in culpa qui officiaan</p>
</div>
<div class="abs card" style="left:796px;top:1610px;width:295px;height:388px">
  <div class="img" style="background:linear-gradient(120deg,#c9c4b4,#8c8b54 45%,#e0552e)" role="img" aria-label="Two engineers in hard hats reviewing plans beside survey equipment"></div>
  <div class="ic"><svg width="40" height="40" viewBox="0 0 40 40"><path d="M8 18a12 12 0 0124 0z" fill="#e0463a"/><rect x="5" y="18" width="30" height="4" fill="#e0463a"/><circle cx="20" cy="30" r="7" fill="none" stroke="#e0463a" stroke-width="4" stroke-dasharray="3 2"/></svg></div>
  <h3>Construction &amp; Engineering</h3>
  <p>Excepteur sint occaecat cupidatat non proident, sunt in culpa qui officiaan</p>
</div>
<div class="abs circ-arrow" style="left:34px;top:1785px;background:#d5d5d5"><svg width="18" height="12" viewBox="0 0 18 12"><path d="M18 6H2M7 1L2 6l5 5" stroke="#fff" stroke-width="2" fill="none"/></svg></div>
<div class="abs circ-arrow" style="left:1129px;top:1785px;background:#555"><svg width="18" height="12" viewBox="0 0 18 12"><path d="M0 6h16M11 1l5 5-5 5" stroke="#fff" stroke-width="2" fill="none"/></svg></div>

<!-- Book a service -->
<div class="abs" style="left:0;top:2093px;width:1200px;height:513px;background:var(--red-dark);clip-path:polygon(0 0,100% 0,100% 337px,600px 513px,0 337px)"></div>
<div class="abs" style="left:0;top:2093px;width:1200px;height:492px;background:linear-gradient(180deg,#5c625c,#626a58);clip-path:polygon(0 0,100% 0,100% 337px,600px 492px,0 337px)" role="img" aria-label="Drone flying over green hilly farmland, with dark overlay"></div>
<div class="abs section-title" style="left:0;top:2166px;width:1200px;font-size:48px;color:#fff"><span class="dot" style="background:#fff"></span>Book a Service Today</div>
<div class="abs kicker" style="left:0;top:2240px;width:1200px;text-align:center;color:#fff">Contact Us</div>
<div class="abs" style="left:215px;top:2280px;width:770px;text-align:center;font-family:'Lato',sans-serif;font-size:15.5px;line-height:26px;color:#fff">Lorem ipsum dolor sit amet, consectetur adipiscing elit, sed do eiusmod tempor incididunt ut labore et dolore magna aliqua. Ut enim ad minim veniam, quis nostrud exercitation ullamco laboris nisi ut aliquip ex ea commodo consequat. Duis aute irure dolor in reprehenderit in voluptate velit esse cillum dolore eu fugiat nulla pariatur.</div>
<div class="abs btn" style="left:475px;top:2414px;height:50px;font-size:17px;background:#fff">
  <span class="label" style="background:#fff;color:var(--red-dark);padding:0 34px 0 26px">Book an Appointment</span><span class="arrow" style="background:var(--red-dark);width:46px;margin-left:-8px;clip-path:polygon(20% 0,100% 0,100% 100%,0 100%)"><svg width="20" height="14" viewBox="0 0 18 12"><path d="M0 6h16M11 1l5 5-5 5" stroke="#fff" stroke-width="1.8" fill="none"/></svg></span>
</div>

<!-- Testimonials -->
<div class="abs section-title" style="left:0;top:2656px;width:1200px;font-size:46px"><span class="dot"></span>What Our Customer Says</div>
<div class="abs kicker" style="left:0;top:2727px;width:1200px;text-align:center">Testimonials</div>

<div class="abs quote" style="left:60px;top:2818px;width:260px">
  <div class="stars">★★★★★</div>
  <p>Temporibus autem quibusdam et aut officiis debitis aut rerum neus saepe facere mus, onis voluptas eveniet ut et voluptates repudae sint et molestiae non lorem recusadae.</p>
  <div class="who"><div class="avatar" role="img" aria-label="Customer portrait"></div><div><b>Calder Winslow</b><i>United States</i></div></div>
</div>
<div class="abs quote" style="left:384px;top:2823px;width:311px;height:342px;border:1.5px solid var(--red);background:#fff;padding:20px 18px 0 18px">
  <div class="stars">★★★★★</div>
  <p>Itaque earum rerum hic tenetur a sapiene delectus, ut aut reiciels volupatibus maiores alias conse uatur aut perferndis doloribus asperiores reiciendis voluptatbus repellat</p>
  <div class="who" style="margin-top:14px"><div class="avatar" style="border:2px solid var(--red)" role="img" aria-label="Customer portrait"></div><div><b>Tessa Rowan</b><i>United States</i></div></div>
</div>
<div class="abs quote" style="left:740px;top:2818px;width:280px">
  <div class="stars">★★★★★</div>
  <p>At vero eos et accusamus et iusto odio dignissimos ducimus qui blaiis praesentium volupttum deleniti atque corrupti quos dolores et quasatque corrupti quos dolores et quas occaecati cupie non provident</p>
  <div class="who"><div class="avatar" role="img" aria-label="Customer portrait"></div><div><b>Orrin Baleford</b><i>United States</i></div></div>
</div>
<div class="abs quote" style="left:1089px;top:2862px;width:280px">
  <div class="stars">★★</div>
  <p>At vero eos et accusamus odio dignissimos ducimus praesentium volupttum atque corrupti quos dolores occaecati cupie non on provident</p>
  <div class="who"><div class="avatar" role="img" aria-label="Customer portrait"></div><div><b>Dara Quinlan</b><i>United States</i></div></div>
</div>

<!-- Footer -->
<div class="abs" style="left:0;top:3280px;width:1200px;height:539px;background:var(--red-dark);clip-path:polygon(0 180px,600px 0,1200px 180px,1200px 100%,0 100%)"></div>
<div class="abs footer" style="left:0;top:3296px;width:1200px;height:523px;background:var(--black);clip-path:polygon(0 164px,600px 20px,1200px 164px,1200px 100%,0 100%)">
  <div class="abs brand" style="left:100px;top:210px;font-size:36px"><span class="dot" style="width:54px;height:54px"></span>Velkora</div>
  <div class="abs" style="left:452px;top:172px">
    <h4>Quick Links</h4>
    <ul><li>› Home</li><li>› About</li><li>› Services</li><li>› Testimonials</li><li>› Contact Us</li></ul>
  </div>
  <div class="abs" style="left:666px;top:172px">
    <h4>Help Links</h4>
    <ul><li>› FAQ</li><li>› Terms of use</li><li>› Privacy Policy</li><li>› Support Links</li><li>› Conditions</li></ul>
  </div>
  <div class="abs" style="left:855px;top:172px;width:300px">
    <h4>Contact Us</h4>
    <div class="contact-row"><span class="ci"><svg width="14" height="18" viewBox="0 0 14 18"><path d="M7 0a7 7 0 00-7 7c0 5 7 11 7 11s7-6 7-11a7 7 0 00-7-7zm0 9.5A2.5 2.5 0 117 4.5a2.5 2.5 0 010 5z" fill="#000"/></svg></span><span>Velkora<br>United States</span></div>
    <div class="contact-row" style="align-items:center"><span class="ci"><svg width="16" height="16" viewBox="0 0 24 24"><path fill="#000" d="M6.6 10.8a15 15 0 006.6 6.6l2.2-2.2c.3-.3.7-.4 1-.2 1.1.4 2.3.6 3.6.6.6 0 1 .4 1 1V20c0 .6-.4 1-1 1C10.6 21 3 13.4 3 4c0-.6.4-1 1-1h3.5c.6 0 1 .4 1 1 0 1.2.2 2.4.6 3.6.1.3 0 .7-.2 1z"/></svg></span><span>+1 555 014 2290</span></div>
    <div class="contact-row" style="align-items:center"><span class="ci"><svg width="16" height="12" viewBox="0 0 24 18"><rect width="24" height="18" rx="2" fill="#000"/><path d="M1 1l11 8 11-8" stroke="#fff" stroke-width="2" fill="none"/></svg></span><span>info@velkora.com</span></div>
  </div>
  <div class="abs" style="left:107px;top:422px;width:980px;height:1px;background:#333"></div>
  <div class="abs" style="left:0;top:460px;width:1200px;text-align:center;font-family:'Lato',sans-serif;font-size:15px;color:#fff">Copyrights@2025.Velkora.All Rights Reserved</div>
</div>
<div class="abs seal" style="left:558px;top:3260px"></div>

</body>
</html>
```